Sophisticated, clean website reflecting my feminine, playful side to sell my abstract art,

I need a website no more than 3 pages to showcase my paintings, a little about me and some contact info. I do abstracts so looking for something a little edgy, yet feminine and current.
Updates

Hi there, These are some artists websites that I Iike: Marnelvoss.com (I like how airy it is) peterwallombry.com garethpolvens.com (I like how it scrolls) I'll need a place for a photo ( a headshot-i do not have it yet so I'll need to be able to upload that later) as well as an area for my bio. Also, it's important that I will be able to upload any new photos and descriptions easily so it should be user friendly. Lastly, I like in a sunny place so would like to have this seem upbeat and playful as that is how i like to paint. thanks-I'm trying to upload my photos now -

Target Market(s)

ppl ages 35-70 who want large scale art for their homes

Industry/Entity Type

art

Coding

Coded - Design and coding required

Number of Pages Required

3 page

Colors

Designer to choose colors to be used in the design.

Requirements
Must have
• photos of my art, a place for my bio, be easy to reach me. tasteful-nothing too "in your face" -my clients are pretty high end and organized. They like clean lines
Nice to have
• sophisticated background, muted tones in the back-similar clean font throughout-no cursive
Should not have
• too many dark areas. Too many blocks of color. Too serious.

```html
<!DOCTYPE html>
<html lang="en">
<head>
<meta charset="utf-8">
<title>Helena Sorrell Art — Menu</title>
<link rel="stylesheet" href="https://fonts.googleapis.com/css2?family=Baloo+2:wght@400;500&display=swap">
<style>
  :root {
    --ink: #16161a;
    --paper: #ffffff;
    --mist: #e4e4e6;
    --faint: #ececee;
    --rose: #e7a3bd;
    --peach: #f6cfae;
    --canvas-tone: #f1eced;
    --footer: #000000;
    --footer-text: #ffffff;
  }
  * { box-sizing: border-box; margin: 0; padding: 0; }
  html, body { width: 1200px; height: 857px; overflow: hidden; background: var(--paper); }
  body { font-family: "Baloo 2", sans-serif; color: var(--ink); position: relative; }

  .menu-screen { position: absolute; left: 0; top: 0; width: 1200px; height: 750px; overflow: hidden; background: var(--paper); }

  .artwork-panel {
    position: absolute; left: 600px; top: 0; width: 600px; height: 750px;
    background:
      radial-gradient(ellipse 70% 50% at 45% 40%, rgba(215,200,205,0.55), transparent 70%),
      linear-gradient(160deg, #f3eff1 0%, #ebe5e7 45%, #eee6e2 100%);
  }

  .peach-glow { position: absolute; left: 0; top: 0; width: 1200px; height: 750px; pointer-events: none; }

  .close-button { position: absolute; left: 42px; top: 15px; width: 50px; height: 50px; }

  .brand-name {
    position: absolute; left: 72px; top: 146px;
    font-size: 26px; font-weight: 400; letter-spacing: 3px; color: var(--mist);
  }

  .headshot {
    position: absolute; left: 42px; top: 200px; width: 142px; height: 113px;
    border-radius: 20px;
    background: linear-gradient(135deg, #f7f4f2 0%, #efe9e5 55%, #f7f5f4 100%);
  }

  .main-nav { position: absolute; left: 187px; top: 190px; list-style: none; }
  .main-nav li { font-size: 31px; font-weight: 500; line-height: 46px; letter-spacing: 1px; }

  .bio {
    position: absolute; left: 42px; top: 337px; width: 330px;
    font-size: 13.3px; line-height: 21px; color: var(--faint);
  }

  .signature {
    position: absolute; left: 42px; top: 444px; width: 108px; height: 26px;
    background: linear-gradient(90deg, #f1f1f2, #f7f7f8); border-radius: 4px;
  }

  .slide-dots { position: absolute; left: 569px; top: 466px; }
  .slide-dots span {
    display: block; width: 9px; height: 9px; margin-bottom: 16px;
    border: 1.3px solid var(--mist); transform: rotate(45deg);
  }
  .slide-dots span.is-active { background: var(--mist); }

  .decor { position: absolute; left: 0; top: 0; width: 1200px; height: 750px; pointer-events: none; }

  .site-footer {
    position: absolute; left: 0; top: 750px; width: 1200px; height: 107px;
    background: var(--footer); color: var(--footer-text);
    font-size: 12.5px; text-align: center; padding-top: 78px;
  }
</style>
</head>
<body>
  <main class="menu-screen">
    <div class="artwork-panel" role="img" aria-label="Abstract floral painting in soft pink, grey and peach tones"></div>

    <svg class="peach-glow" viewBox="0 0 1200 750" aria-hidden="true">
      <circle cx="1200" cy="1010" r="640" fill="var(--peach)" opacity="0.45"/>
    </svg>

    <svg class="close-button" viewBox="0 0 50 50" aria-label="Close menu">
      <line x1="1" y1="1" x2="49" y2="49" stroke="var(--ink)" stroke-width="2.2"/>
      <line x1="49" y1="1" x2="1" y2="49" stroke="var(--ink)" stroke-width="2.2"/>
    </svg>

    <div class="brand-name">Helena Sorrell</div>

    <div class="headshot" role="img" aria-label="Headshot of the artist"></div>

    <ul class="main-nav">
      <li>ABOUT</li>
      <li>PORTFOLIO</li>
      <li>CONTACT</li>
    </ul>

    <p class="bio">Lorem ipsum dolor sit amet, consectetuer adipiscing elit. Aenean commodo ligula eget dolor. Aenean massa. Cum sociis natoque penatibus et magnis dis parturient montes, nascetur ridiculus mus.</p>

    <div class="signature" role="img" aria-label="Artist's handwritten signature"></div>

    <div class="slide-dots">
      <span class="is-active"></span><span></span><span></span><span></span><span></span>
    </div>

    <svg class="decor" viewBox="0 0 1200 750" aria-hidden="true">
      <circle cx="117" cy="655" r="75" fill="none" stroke="#e9e9eb" stroke-width="1"/>
      <g stroke="#e1e1e3" stroke-width="1.5" fill="none">
        <line x1="101" y1="671" x2="133" y2="639"/>
        <polyline points="115,639 133,639 133,657"/>
      </g>
      <line x1="308" y1="675" x2="368" y2="616" stroke="var(--rose)" stroke-width="1.4"/>
      <circle cx="572" cy="858" r="247" fill="none" stroke="var(--rose)" stroke-width="1.4"/>
      <line x1="785" y1="184" x2="845" y2="125" stroke="var(--rose)" stroke-width="1.4"/>
      <circle cx="1200" cy="-20" r="360" fill="none" stroke="var(--rose)" stroke-width="1.4"/>
    </svg>
  </main>

  <footer class="site-footer">©2022 Helena Sorrell Art. All rights reserved.</footer>
</body>
</html>
```